Kestrel Home Business Card Design

We need a business card for a Building company based in Queensland, Australia. Our colours are orange black and we do base all our homes design names and other aspect of our business on astrology. We want the consumer to perceive the company as professional and to attract investors to our company.We have over 20 years in the building industry.We pride ourselves on our innovation of designs and making the building process for anyone from families to investor a smooth and simple experience.
Business
Amelia Prichard0411752116PO Box 454, Mudgeerbaameliaprichard@zodiachomes.com

```html
<!DOCTYPE html>
<html lang="en">
<head>
<meta charset="utf-8">
<title>Kestrel Homes Business Card</title>
<link rel="stylesheet" href="https://fonts.googleapis.com/css2?family=Open+Sans:wght@400;700&display=swap">
<style>
  :root {
    --orange: #f39322;
    --black: #0b0b0b;
    --white: #ffffff;
    --backdrop: #e9e6e1;
    --ink: #1c1c1c;
  }
  * { margin: 0; padding: 0; box-sizing: border-box; }
  html, body {
    width: 1200px; height: 1200px; overflow: hidden;
    background: var(--backdrop);
    font-family: "Open Sans", Arial, sans-serif;
  }
  .canvas {
    width: 1200px; height: 1200px;
    display: flex; flex-direction: column; align-items: center; justify-content: center;
    gap: 40px;
  }
  .card {
    position: relative;
    width: 900px; height: 540px;
    overflow: hidden;
    box-shadow: 0 6px 18px rgba(0,0,0,0.18);
  }
  /* Front */
  .card-front { background: var(--black); }
  .front-band {
    position: absolute; left: 0; right: 0; top: 175px; height: 190px;
    background: var(--orange);
    display: flex; align-items: center; padding-left: 60px; gap: 28px;
  }
  .brand-dot {
    width: 130px; height: 130px; border-radius: 50%;
    flex: none;
  }
  .front-band .brand-dot { background: var(--black); }
  .brand-name {
    font-weight: 700; color: var(--ink);
    letter-spacing: -0.5px; white-space: nowrap;
  }
  .front-band .brand-name { font-size: 72px; }
  /* Back */
  .card-back { background: var(--black); }
  .back-top {
    position: absolute; left: 0; right: 0; top: 0; height: 300px;
    background: var(--white);
    border-bottom: 4px solid var(--orange);
    display: flex; align-items: center; padding-left: 150px; gap: 26px;
  }
  .back-top .brand-dot { background: var(--orange); width: 140px; height: 140px; }
  .back-top .brand-name { font-size: 68px; }
  .holder-name {
    position: absolute; left: 60px; top: 360px;
    color: var(--orange); font-size: 30px; letter-spacing: 2px;
  }
  .contact-list {
    position: absolute; right: 40px; top: 380px;
    list-style: none;
    color: var(--white); font-size: 22px; letter-spacing: 1.5px;
    text-align: right;
  }
  .contact-list li {
    display: flex; justify-content: flex-end; align-items: center; gap: 14px;
    height: 36px;
  }
  .contact-icon { width: 18px; height: 18px; flex: none; }
</style>
</head>
<body>
<main class="canvas">
  <section class="card card-front" aria-label="Business card front">
    <div class="front-band">
      <span class="brand-dot" aria-hidden="true"></span>
      <span class="brand-name">Kestrel Homes</span>
    </div>
  </section>

  <section class="card card-back" aria-label="Business card back">
    <div class="back-top">
      <span class="brand-dot" aria-hidden="true"></span>
      <span class="brand-name">Kestrel Homes</span>
    </div>
    <p class="holder-name">Harriet Colvane</p>
    <ul class="contact-list">
      <li>0487309625
        <svg class="contact-icon" viewBox="0 0 24 24" aria-hidden="true"><path fill="#f39322" d="M6.6 10.8a15.1 15.1 0 0 0 6.6 6.6l2.2-2.2c.3-.3.7-.4 1-.2 1.1.4 2.3.6 3.6.6.6 0 1 .4 1 1V20c0 .6-.4 1-1 1A17 17 0 0 1 3 4c0-.6.4-1 1-1h3.5c.6 0 1 .4 1 1 0 1.3.2 2.5.6 3.6.1.3 0 .7-.2 1z"/></svg>
      </li>
      <li>PO Box 872, Coralbrook
        <svg class="contact-icon" viewBox="0 0 24 24" aria-hidden="true"><path fill="#f39322" d="M12 2a7 7 0 0 0-7 7c0 5.2 7 13 7 13s7-7.8 7-13a7 7 0 0 0-7-7zm0 9.5A2.5 2.5 0 1 1 12 6.5a2.5 2.5 0 0 1 0 5z"/></svg>
      </li>
      <li>harrietcolvane@kestrelhomes.example
        <svg class="contact-icon" viewBox="0 0 24 24" aria-hidden="true"><rect x="3" y="5" width="18" height="14" fill="none" stroke="#f39322" stroke-width="2"/><path d="M3 6l9 7 9-7" fill="none" stroke="#f39322" stroke-width="2"/></svg>
      </li>
    </ul>
  </section>
</main>
</body>
</html>
```